Professional violinist needs business cards

I am trying to attract the following jobs:
-private violin lessons (primarily classical)
-performance gigs (weddings, birthday parties, funerals, etc.)
-collaborations with other artists (studio recordings, performances)

I want to communicate that I have a very high standard of excellence for my work, but I also love people and celebrations.
Values/style words I like are:
love, joy, peace, fun, beauty, authenticity, excellence, warmth, refined/sleek, free spirited. If that's too confusing, just ignore :)

I will attach my favorite business card template that I could find on Canva. The lines are supposed to be like a music staff, which I think is really cool, but I also don't want it to look too busy. I like the simple black and white--I think it looks sharp--but I also am open to other ideas. I also have seen business cards with pictures included that looked great, so I attached an image that could be used as well.

I am also attaching a file that I made of my initials that could be used as a logo, but I'm not sure if it should be included.

Information on the card:
-My name (18 letters total)
-"violinist"
-phone number, email, website

Thank you!

```html
<!DOCTYPE html>
<html lang="en">
<head>
<meta charset="utf-8">
<title>Marian Ellsworth – Violinist Business Card</title>
<link href="https://fonts.googleapis.com/css2?family=Open+Sans:wght@400;600;700&display=swap" rel="stylesheet">
<style>
  :root {
    --page-bg: #2a2a2a;
    --card-black: #0f0f0f;
    --accent-peach: #f3b47c;
    --text-white: #f4f1ec;
    --text-grey: #a9a6a2;
    --mark-grey: #8e8e8e;
    --stone-light: #8a7f6a;
    --stone-mid: #5c5446;
    --stone-dark: #2b2721;
    --wood-light: #9a5e32;
    --wood-mid: #74421f;
    --wood-dark: #3a1f0d;
  }
  * { box-sizing: border-box; margin: 0; padding: 0; }
  html, body {
    width: 1200px; height: 1108px; overflow: hidden;
    background: var(--page-bg);
    font-family: "Open Sans", Arial, sans-serif;
  }
  .canvas {
    position: relative; width: 1200px; height: 1108px;
    display: flex; justify-content: center; align-items: center; gap: 60px;
  }
  .card {
    position: relative; width: 480px; height: 800px;
    border-radius: 22px; overflow: hidden;
    box-shadow: 0 18px 40px rgba(0,0,0,.45);
  }

  /* Front */
  .card--front { background: var(--stone-dark); }
  .front-photo {
    position: absolute; inset: 0;
    background:
      radial-gradient(ellipse 40% 55% at 66% 55%, #0c0b0b 0 60%, transparent 75%),
      linear-gradient(160deg, var(--stone-light) 0%, var(--stone-mid) 45%, var(--stone-dark) 80%, #141210 100%);
  }
  .front-info {
    position: absolute; left: 38px; bottom: 110px;
    color: var(--text-white);
  }
  .front-name {
    font-size: 34px; font-weight: 600; color: var(--accent-peach);
    letter-spacing: .3px; line-height: 1.1;
  }
  .front-role { font-size: 24px; font-weight: 600; margin: 4px 0 22px; }
  .contact-list { list-style: none; }
  .contact-item {
    display: flex; align-items: center; gap: 12px;
    font-size: 23px; font-weight: 600; line-height: 1.45;
  }
  .contact-icon { width: 26px; height: 26px; flex: none; }

  /* Back */
  .card--back { background: var(--card-black); }
  .back-photo {
    position: absolute; right: 30px; top: 110px; width: 130px; height: 630px;
    border-radius: 30px 30px 65px 65px;
    background: linear-gradient(180deg, var(--wood-mid) 0%, var(--wood-light) 45%, var(--wood-mid) 75%, var(--wood-dark) 100%);
    opacity: .85;
  }
  .brand-name {
    position: absolute; left: 44px; top: 170px;
    font-size: 44px; font-weight: 600; line-height: 1.1;
    color: var(--mark-grey);
  }
  .service-list {
    position: absolute; left: 44px; bottom: 80px; width: 265px;
    list-style: none;
  }
  .service { margin-top: 22px; }
  .service-title {
    font-size: 21px; font-weight: 700; color: var(--text-white); line-height: 1.25;
  }
  .service-note {
    font-size: 17px; font-weight: 400; color: var(--text-grey); line-height: 1.35;
    margin-top: 2px;
  }
</style>
</head>
<body>
<main class="canvas">

  <section class="card card--front">
    <div class="front-photo" role="img" aria-label="Photo of the violinist in a black dress holding her violin and bow beside a stone wall and stair rail"></div>
    <div class="front-info">
      <h1 class="front-name">Marian Ellsworth</h1>
      <p class="front-role">Violinist</p>
      <ul class="contact-list">
        <li class="contact-item">
          <svg class="contact-icon" viewBox="0 0 24 24" fill="none" stroke="var(--accent-peach)" stroke-width="1.8">
            <rect x="2" y="2" width="20" height="20" rx="3"/>
            <path d="M8 6c-1 1-1 3 1 6s4 5 6 5l1.5-1.5-2.5-2-1.2 1c-1.2-.6-2.6-2-3.2-3.2l1-1.2-2-2.5z" fill="var(--accent-peach)" stroke="none"/>
          </svg>
          <span>044-555 210 347</span>
        </li>
        <li class="contact-item">
          <svg class="contact-icon" viewBox="0 0 24 24" fill="none" stroke="var(--accent-peach)" stroke-width="1.8">
            <rect x="2" y="5" width="20" height="14" rx="1"/>
            <path d="M2 5l10 8 10-8"/>
          </svg>
          <span>hello@marianviolin.com</span>
        </li>
        <li class="contact-item">
          <svg class="contact-icon" viewBox="0 0 24 24" fill="none" stroke="var(--accent-peach)" stroke-width="1.6">
            <circle cx="12" cy="12" r="10"/>
            <ellipse cx="12" cy="12" rx="4.5" ry="10"/>
            <path d="M2 12h20M4 7h16M4 17h16"/>
          </svg>
          <span>www.marianviolin.com</span>
        </li>
      </ul>
    </div>
  </section>

  <section class="card card--back">
    <div class="back-photo" role="img" aria-label="Photo of a wooden ukulele standing upright on a dark background"></div>
    <p class="brand-name">Marian<br>Ellsworth</p>
    <ul class="service-list">
      <li class="service">
        <p class="service-title">Private violin lessons</p>
        <p class="service-note">(primarily classical)</p>
      </li>
      <li class="service">
        <p class="service-title">Performance gigs</p>
        <p class="service-note">(weddings, birthday parties, funerals, etc.)</p>
      </li>
      <li class="service">
        <p class="service-title">Collaborations with other artists</p>
        <p class="service-note">(studio recordings, performances)</p>
      </li>
    </ul>
  </section>

</main>
</body>
</html>
```